Poster for Kirtan Music Event

Design (3) 24" x 36" Posters

I have provided a sample a friend did in Australia: ( Picture No. 4 )

Use all the text on sample poster except the replacement changes below.

Replace with the following text as this is for different location:
Replacement Text:

Every Friday Night 7:00pm-8:30pm
Kealoha Pilates & Movement Studio
947 Hollister Rd Paia

Free Kirtan Experience! or Free Event
Mohan Priya Sevi & Companions

Optional Text:

A evening of music, singing of spiritual mantras, and refreshments

Bring flowers, musical instruments, friends, or just come with an open heart.

Meditate on transcendental sounds that provide rest for the mind & heart"

An evening of music & singing of sacred mantra's

```html
<!DOCTYPE html>
<html lang="en">
<head>
<meta charset="utf-8">
<title>Kirtan Experience Poster</title>
<link rel="stylesheet" href="https://fonts.googleapis.com/css2?family=Oswald:wght@500;600&family=Raleway:wght@200;300&display=swap">
<style>
  :root {
    --magenta: #c2307f;
    --pink: #e15ba3;
    --plum: #7a2a86;
    --violet: #5a2a8c;
    --navy: #27306e;
    --deep: #351244;
    --white: #ffffff;
    --gold: #f2c95a;
  }
  html, body { margin: 0; padding: 0; overflow: hidden; background: var(--deep); }
  .poster {
    position: relative;
    width: 800px;
    height: 1200px;
    overflow: hidden;
    background: linear-gradient(160deg, var(--plum) 0%, var(--magenta) 40%, var(--violet) 70%, var(--deep) 100%);
  }
  .artwork { position: absolute; inset: 0; }
  .rotated { position: absolute; white-space: nowrap; color: var(--white); transform-origin: 0 0; }
  .title {
    font-family: "Raleway", sans-serif;
    font-weight: 200;
    text-transform: uppercase;
    line-height: 1;
  }
  .title-kirtan { left: 30px; top: 436px; font-size: 150px; letter-spacing: -4px; transform: rotate(-45deg); transform-origin: 0 100%; margin-top: -150px; }
  .title-experience { left: 420px; top: 0; font-size: 96px; letter-spacing: -2px; transform: rotate(45deg); }
  .schedule {
    left: 172px; top: 400px;
    font-family: "Oswald", sans-serif;
    text-transform: uppercase;
    transform: rotate(45deg);
    line-height: 1.05;
  }
  .schedule-time { font-size: 38px; font-weight: 600; }
  .schedule-venue { font-size: 21px; font-weight: 500; margin-left: 4px; }
  .host {
    left: 540px; top: 884px;
    font-family: "Oswald", sans-serif;
    text-transform: uppercase;
    transform: rotate(-45deg);
    line-height: 1.12;
  }
  .host-offer { font-size: 27px; font-weight: 500; }
  .host-name { font-size: 38px; font-weight: 600; }
</style>
</head>
<body>
<main class="poster">
  <svg class="artwork" width="800" height="1200" viewBox="0 0 800 1200">
    <defs>
      <linearGradient id="deityLeft" x1="0" y1="0" x2="1" y2="1">
        <stop offset="0" stop-color="#b2567e"/><stop offset="1" stop-color="#6f2b6a"/>
      </linearGradient>
      <linearGradient id="deityRight" x1="0" y1="0" x2="1" y2="1">
        <stop offset="0" stop-color="#c88aa6"/><stop offset="1" stop-color="#4a3b8c"/>
      </linearGradient>
      <radialGradient id="drumGlow" cx="0.35" cy="0.3" r="0.7">
        <stop offset="0" stop-color="#ffe9a0"/><stop offset="0.45" stop-color="#e8a24a"/><stop offset="1" stop-color="#b24a6e" stop-opacity="0.2"/>
      </radialGradient>
      <linearGradient id="coupleTone" x1="0" y1="0" x2="0" y2="1">
        <stop offset="0" stop-color="#d9a0a6"/><stop offset="1" stop-color="#8a3d78"/>
      </linearGradient>
      <linearGradient id="mono" x1="0" y1="0" x2="1" y2="1">
        <stop offset="0" stop-color="#e2e2e2"/><stop offset="1" stop-color="#555"/>
      </linearGradient>
    </defs>

    <g class="tiles" transform="rotate(45 400 600)" opacity="0.35">
      <rect x="120" y="120" width="140" height="140" fill="#3a2f8f"/>
      <rect x="400" y="260" width="140" height="140" fill="#e66fb0"/>
      <rect x="260" y="540" width="140" height="140" fill="#2a2466"/>
      <rect x="540" y="540" width="140" height="140" fill="#9b3ea0"/>
      <rect x="120" y="680" width="140" height="140" fill="#d33a8c"/>
      <rect x="680" y="400" width="140" height="140" fill="#3b4ea6"/>
      <rect x="400" y="820" width="140" height="140" fill="#5a1f6a"/>
      <rect x="-20" y="400" width="140" height="140" fill="#f07ab8"/>
      <rect x="820" y="680" width="140" height="140" fill="#2d2a7a"/>
    </g>

    <rect class="art-deity-left" x="0" y="0" width="290" height="330" fill="url(#deityLeft)" opacity="0.75" role="img" aria-label="Painted portrait of a deity playing the flute"/>
    <rect class="art-deity-right" x="560" y="0" width="240" height="300" fill="url(#deityRight)" opacity="0.7" role="img" aria-label="Painted portrait of a devotional figure"/>
    <rect class="art-drum" x="0" y="600" width="440" height="600" fill="url(#drumGlow)" opacity="0.9" role="img" aria-label="Close-up photo of hands playing a mridanga drum"/>
    <polygon class="art-couple" points="400,900 800,900 800,1200 300,1200" fill="url(#coupleTone)" opacity="0.8" role="img" aria-label="Painting of a divine couple"/>

    <polygon class="schedule-band" points="560,765 760,965 640,1085 440,885" fill="var(--navy)" opacity="0.55"/>

    <g class="performer-photos">
      <polygon points="324,244 374,294 324,344 274,294" fill="url(#mono)" role="img" aria-label="Photo of a musician"/>
      <polygon points="504,244 554,294 504,344 454,294" fill="url(#mono)" role="img" aria-label="Photo of musicians playing"/>
      <polygon points="516,418 566,468 516,518 466,468" fill="url(#mono)" role="img" aria-label="Photo of a guitarist"/>
      <polygon points="672,406 722,456 672,506 622,456" fill="url(#mono)" role="img" aria-label="Photo of a singer"/>
      <polygon points="672,574 722,624 672,674 622,624" fill="url(#mono)" role="img" aria-label="Photo of a vocalist"/>
    </g>

    <g class="rules" stroke="#ffffff" stroke-width="4" fill="none">
      <line x1="0" y1="590" x2="590" y2="0"/>
      <line x1="0" y1="300" x2="300" y2="0"/>
      <line x1="150" y1="355" x2="600" y2="805"/>
      <line x1="0" y1="370" x2="520" y2="890"/>
      <line x1="470" y1="0" x2="800" y2="330"/>
      <line x1="560" y1="1200" x2="800" y2="960"/>
      <line x1="800" y1="600" x2="200" y2="1200"/>
      <line x1="0" y1="1030" x2="170" y2="1200"/>
    </g>
  </svg>

  <div class="rotated title title-kirtan">Kirtan</div>
  <div class="rotated title title-experience">Experience</div>

  <div class="rotated schedule">
    <div class="schedule-time">Every Friday Night 7:00pm-8:30pm</div>
    <div class="schedule-venue">Kealoha Pilates &amp; Movement Studio 947 Hollister Rd Paia</div>
  </div>

  <div class="rotated host">
    <div class="host-offer">Free Kirtan Experience</div>
    <div class="host-name">Mohan Priya Sevi</div>
    <div class="host-name">&amp; Companions</div>
  </div>
</main>
</body>
</html>
```